The Copper Kite Website Redesign

I want a new design and website for www.thecopperkitebrookvale.com where part of the home page includes our daily specials from our POS Toast to be pulled from API. I have included photos and links to give you a better feel for the style of our restaurant.

Coding

Coded - Design and coding required

```html
<!DOCTYPE html>
<html lang="en">
<head>
<meta charset="utf-8">
<title>The Copper Kite Brookvale</title>
<link href="https://fonts.googleapis.com/css2?family=Gochi+Hand&family=Poppins:wght@400;500;600&display=swap" rel="stylesheet">
<style>
:root{
  --orange:#f28a11;
  --ink:#111111;
  --dark:#1b1b1b;
  --panel:#262626;
  --light:#f3f3f3;
  --white:#ffffff;
  --text:#333333;
  --line:#d9d9d9;
}
*{box-sizing:border-box;margin:0;padding:0}
html,body{width:1200px;height:3592px;overflow:hidden}
body{position:relative;font-family:"Poppins",sans-serif;color:var(--text);background:var(--white)}
.hand{font-family:"Gochi Hand",cursive}
.btn{position:absolute;background:var(--orange);color:var(--white);font-size:13px;font-weight:600;text-transform:uppercase;border-radius:22px;padding:0 26px;height:40px;line-height:40px;box-shadow:0 4px 0 #a85d05;letter-spacing:.5px;white-space:nowrap}
.photo{position:absolute;border-radius:26px;box-shadow:8px 10px 0 var(--orange)}

/* nav */
.nav{position:absolute;top:0;left:0;width:1200px;height:64px;background:var(--white)}
.brand{position:absolute;left:98px;top:10px;font-size:30px;color:var(--ink);line-height:40px;white-space:nowrap}
.nav-links{position:absolute;left:398px;top:22px;display:flex;gap:34px;font-size:13px;font-weight:500;color:var(--ink)}
.nav-links .active{color:var(--orange)}
.nav .btn{left:986px;top:16px;height:32px;line-height:32px;font-size:11px;padding:0 20px;box-shadow:none}

/* hero */
.hero{position:absolute;top:64px;left:0;width:1200px;height:456px;background:linear-gradient(90deg,#121212 0%,#1e1e1e 55%,#3a2a1e 100%)}
.hero-photo{position:absolute;right:0;top:0;width:560px;height:456px;background:radial-gradient(circle at 60% 40%,#b8562a 0%,#7a3316 30%,#2a1a12 65%,transparent 85%)}
.hero h1{position:absolute;left:112px;top:112px;font-family:"Gochi Hand",cursive;font-weight:400;font-size:50px;color:var(--white);white-space:nowrap}
.hero h1 span{color:var(--orange)}
.hero h2{position:absolute;left:112px;top:176px;font-family:"Gochi Hand",cursive;font-weight:400;font-size:40px;color:var(--white);white-space:nowrap}
.hero .btn{left:112px;top:280px}

/* about */
.about-photo{left:116px;top:600px;width:372px;height:460px;background:linear-gradient(160deg,#c07a3a,#6b3b1c 55%,#2b1a10)}
.section-title{position:absolute;font-family:"Gochi Hand",cursive;font-weight:400;font-size:46px;color:var(--ink);white-space:nowrap}
.section-title span{color:var(--orange)}
.about-title{left:582px;top:600px}
.about-text{position:absolute;left:582px;top:678px;width:500px;font-size:14.5px;line-height:28px;color:#444}
.about .btn{left:582px;top:1024px}

/* menu */
.menu{position:absolute;top:1160px;left:0;width:1200px;height:920px;background:linear-gradient(180deg,#1c1c1c,#121212)}
.menu-title{left:0;width:1200px;text-align:center;top:52px;color:var(--white)}
.card{position:absolute;border-radius:18px;overflow:hidden}
.tag{position:absolute;background:var(--white);color:var(--ink);font-size:12.5px;font-weight:600;text-transform:uppercase;padding:8px 16px;border-radius:4px;white-space:nowrap}
.tag.alt{background:var(--orange);color:var(--white)}

/* specials */
.specials-title{left:112px;top:2168px}
.dish{position:absolute;left:112px;top:2250px;font-family:"Gochi Hand",cursive;font-weight:400;font-size:44px;color:var(--ink);white-space:nowrap}
.specials-text{position:absolute;left:112px;top:2330px;width:470px;font-size:14.5px;line-height:28px;color:#444}
.specials .btn{left:112px;top:2568px}
.special-photo{left:704px;top:2164px;width:372px;height:532px;background:linear-gradient(150deg,#e8874e,#c4522a 50%,#7d2f18)}

/* faq */
.faq{position:absolute;top:2720px;left:0;width:1200px;height:510px;background:var(--light)}
.faq-title{left:0;width:1200px;text-align:center;top:52px}
.q{position:absolute;width:440px;height:44px;background:var(--white);border:1px solid var(--line);font-size:12.5px;font-weight:500;color:var(--ink);text-transform:uppercase;line-height:42px;padding-left:18px}
.q svg{position:absolute;right:14px;top:12px}
.q.open{height:160px;background:var(--orange);color:var(--white);border-color:var(--orange)}
.q.open p{text-transform:none;font-weight:400;font-size:13px;line-height:22px;padding-right:50px;margin-top:-4px}
.faq .btn{left:490px;top:420px}

/* footer */
.footer{position:absolute;top:3230px;left:0;width:1200px;height:362px;background:var(--ink);color:var(--white)}
.footer .brand{left:108px;top:60px;font-size:42px;color:var(--white)}
.copy{position:absolute;left:108px;top:170px;font-size:13px;line-height:24px;font-weight:500;text-transform:uppercase}
.copy span{color:var(--orange)}
.col-title{position:absolute;top:60px;font-size:17px;font-weight:600;color:var(--orange);text-transform:uppercase;letter-spacing:1px}
.links{position:absolute;left:412px;top:104px;font-size:12px;line-height:30px;text-transform:uppercase;list-style:none}
.contact{position:absolute;left:670px;top:100px;font-size:12px;list-style:none;text-transform:uppercase}
.contact li{display:flex;align-items:center;gap:14px;height:50px;white-space:nowrap}
.contact svg{flex:none}
</style>
</head>
<body>

<header class="nav">
  <div class="brand hand">The Copper Kite</div>
  <nav class="nav-links">
    <span class="active">HOME</span><span>ABOUT US</span><span>MENU</span><span>RETAIL</span><span>PRESS</span><span>CONTACT US</span>
  </nav>
  <span class="btn">Reserve Now</span>
</header>

<section class="hero">
  <div class="hero-photo" role="img" aria-label="Plate of spaghetti with tomato sauce and basil on a dark table"></div>
  <h1>Welcome to The <span>Copper Kite</span> Brookvale</h1>
  <h2>Fresh plates, made from scratch daily.</h2>
  <span class="btn">View Our Menu</span>
</section>

<section class="about">
  <div class="photo about-photo" role="img" aria-label="Waffles topped with fruit and cream on a diner table"></div>
  <h2 class="section-title about-title">About <span>Copper Kite Brookvale</span></h2>
  <p class="about-text">The doors of The Copper Kite: a cozy corner kitchen were eagerly thrown open for the first time on March 14th 2011. We welcomed our first customers and started our magnificent life as a business that continues on through today. Along with our beloved and inquisitive customers came the many questions of our origin. The most important of which we will address right here and now – "Why?" they asked "Why did you name your restaurant The Copper Kite?" We always swore we would make up some exciting folklore tale of the origin of our now-venerated name.</p>
  <span class="btn">Learn More</span>
</section>

<section class="menu">
  <h2 class="section-title menu-title">The Copper Kite <span>Menu</span></h2>
  <div class="card" style="left:120px;top:220px;width:310px;height:400px;background:linear-gradient(160deg,#6d5a4a,#2e2520)" role="img" aria-label="Hands cracking eggs into a pan"></div>
  <span class="tag" style="left:170px;top:390px">All Things Eggs</span>
  <div class="card" style="left:445px;top:220px;width:310px;height:400px;background:radial-gradient(circle at 50% 45%,#c98b5a,#8a4f2b 55%,#3b2416)" role="img" aria-label="Pancakes drizzled with chocolate sauce"></div>
  <span class="tag" style="left:510px;top:390px">Oh, Sugar Shack!</span>
  <div class="card" style="left:775px;top:180px;width:300px;height:175px;background:radial-gradient(circle,#7fa34a,#3e5a26 60%,#1a1a1a)" role="img" aria-label="Fresh green salad in a bowl"></div>
  <span class="tag" style="left:855px;top:250px">Green Things</span>
  <div class="card" style="left:775px;top:370px;width:300px;height:230px;background:radial-gradient(circle at 50% 50%,#c98a3e,#6b3a18 55%,#1a1a1a 80%)" role="img" aria-label="Burger on a dark background"></div>
  <span class="tag alt" style="left:855px;top:455px">Between Bread</span>
  <div class="card" style="left:120px;top:640px;width:635px;height:240px;background:radial-gradient(circle at 72% 50%,#b06a35,#5a3320 35%,#1c1c1c 65%)" role="img" aria-label="Chermoula chicken with vegetables"></div>
  <span class="tag" style="left:220px;top:756px">Chermoula Chicken</span>
  <div class="card" style="left:775px;top:650px;width:300px;height:195px;background:linear-gradient(160deg,#f2f2f2,#e2b36c 60%,#b77a3a)" role="img" aria-label="Grilled sandwich on a plate"></div>
  <span class="tag" style="left:866px;top:720px">Other Stuff</span>
</section>

<section class="specials">
  <h2 class="section-title specials-title">Today's <span>Specials</span></h2>
  <h3 class="dish">Grilled Herb-Crusted Salmon</h3>
  <p class="specials-text">Lorem ipsum dolor sit amet, consectetur adipiscing elit, sed do eiusmod tempor incididunt ut labore et dolore magna aliqua. Ut enim ad minim veniam, quis nostrud exercitation ullamco laboris nisi ut aliquip ex ea commodo consequat. Duis aute irure dolor in reprehenderit in voluptate velit esse cillum dolore eu fugiat nulla pariatur.</p>
  <span class="btn">View Our Special</span>
  <div class="photo special-photo" role="img" aria-label="Grilled salmon fillet with lemon slices"></div>
</section>

<section class="faq">
  <h2 class="section-title faq-title">Frequently Asked <span>Questions</span></h2>
  <div class="q" style="left:120px;top:150px">Do you take reservations?<svg width="20" height="20" viewBox="0 0 20 20"><circle cx="10" cy="10" r="8.5" fill="none" stroke="#111" stroke-width="1.2"/><path d="M10 6v8M6 10h8" stroke="#111" stroke-width="1.4"/></svg></div>
  <div class="q" style="left:120px;top:210px">Do you deliver?<svg width="20" height="20" viewBox="0 0 20 20"><circle cx="10" cy="10" r="8.5" fill="none" stroke="#111" stroke-width="1.2"/><path d="M10 6v8M6 10h8" stroke="#111" stroke-width="1.4"/></svg></div>
  <div class="q" style="left:120px;top:270px">Why didn't you answer my question?<svg width="20" height="20" viewBox="0 0 20 20"><circle cx="10" cy="10" r="8.5" fill="none" stroke="#111" stroke-width="1.2"/><path d="M10 6v8M6 10h8" stroke="#111" stroke-width="1.4"/></svg></div>
  <div class="q" style="left:635px;top:150px">Do you do carry-out?<svg width="20" height="20" viewBox="0 0 20 20"><circle cx="10" cy="10" r="8.5" fill="none" stroke="#111" stroke-width="1.2"/><path d="M10 6v8M6 10h8" stroke="#111" stroke-width="1.4"/></svg></div>
  <div class="q open" style="left:635px;top:210px">How large is your restaurant?<svg width="20" height="20" viewBox="0 0 20 20"><circle cx="10" cy="10" r="8.5" fill="none" stroke="#fff" stroke-width="1.2"/><path d="M6 10h8" stroke="#fff" stroke-width="1.4"/></svg><p>We are a pretty compact space but we have seating for about 60 people.</p></div>
  <span class="btn">View More Questions</span>
</section>

<footer class="footer">
  <div class="brand hand">The Copper Kite</div>
  <p class="copy">© 2025 <span>The Copper Kite</span><br>All rights reserved</p>
  <h4 class="col-title" style="left:412px">Quick Links</h4>
  <ul class="links"><li>Home</li><li>About Us</li><li>Menu</li><li>Retail</li><li>Press</li><li>Contact Us</li></ul>
  <h4 class="col-title" style="left:670px">Contact Us</h4>
  <ul class="contact">
    <li><svg width="30" height="30" viewBox="0 0 30 30"><circle cx="15" cy="15" r="14" fill="none" stroke="#fff"/><path d="M11 9l3 3-2 2a9 9 0 0 0 4 4l2-2 3 3-2 2c-5 0-10-5-10-10z" fill="#fff"/></svg>(555) 214-3820</li>
    <li><svg width="30" height="30" viewBox="0 0 30 30"><circle cx="15" cy="15" r="14" fill="none" stroke="#fff"/><rect x="9" y="11" width="12" height="9" fill="none" stroke="#fff"/><path d="M9 11l6 5 6-5" fill="none" stroke="#fff"/></svg>eat@thecopperkitebrookvale.com</li>
    <li><svg width="30" height="30" viewBox="0 0 30 30"><circle cx="15" cy="15" r="14" fill="none" stroke="#fff"/><path d="M15 8a5 5 0 0 0-5 5c0 4 5 9 5 9s5-5 5-9a5 5 0 0 0-5-5z" fill="none" stroke="#fff"/><circle cx="15" cy="13" r="1.8" fill="#fff"/></svg>1840 Harbor Lane Brookvale, Oregon 97301</li>
    <li><svg width="30" height="30" viewBox="0 0 30 30"><circle cx="15" cy="15" r="14" fill="none" stroke="#fff"/><circle cx="15" cy="15" r="7" fill="none" stroke="#fff"/><path d="M15 11v4l3 2" fill="none" stroke="#fff"/></svg>Tuesday - Sunday 7 a.m. - 2 p.m.</li>
  </ul>
</footer>

</body>
</html>
```